Wine label

We are a patriotic wine company that supports the military and police. www.harborcrestcellars.com We are looking for a commemorative wine label for the 250th anniversary of the United States. We like bad ass labels you can see our other labels online

Requirements
Should not have
• does not need harbor crest cellars in the label

```html
<!DOCTYPE html>
<html lang="en">
<head>
<meta charset="utf-8">
<title>250 Years of Unyielding Spirit – Commemorative Wine Label</title>
<link rel="stylesheet" href="https://fonts.googleapis.com/css2?family=Abril+Fatface&family=Oswald:wght@500;600&display=swap">
<style>
  :root {
    --label-black: #1e1e1e;
    --cream: #e4dec6;
    --art-brown: #8a6f45;
    --art-dark: #3a2e1e;
    --art-red: #9b3a34;
    --art-blue: #34405e;
  }
  * { margin: 0; padding: 0; box-sizing: border-box; }
  html, body {
    width: 1200px;
    height: 490px;
    overflow: hidden;
    background: var(--label-black);
  }
  .label {
    display: block;
    width: 1200px;
    height: 490px;
  }
  .tagline {
    font-family: "Oswald", sans-serif;
    font-weight: 500;
    font-size: 9px;
    fill: var(--cream);
  }
  .numeral {
    font-family: "Abril Fatface", serif;
    font-size: 92px;
    fill: var(--cream);
  }
  .headline {
    font-family: "Oswald", sans-serif;
    font-weight: 600;
    fill: var(--cream);
  }
  .headline--years { font-size: 46px; }
  .headline--unyielding { font-size: 37px; }
  .headline--spirit { font-size: 64px; }
</style>
</head>
<body>
<svg class="label" viewBox="0 0 1200 490" xmlns="http://www.w3.org/2000/svg">
  <defs>
    <linearGradient id="art-tones" x1="0" y1="0" x2="0" y2="1">
      <stop offset="0" stop-color="var(--art-blue)"/>
      <stop offset="0.25" stop-color="var(--art-red)"/>
      <stop offset="0.55" stop-color="var(--art-brown)"/>
      <stop offset="1" stop-color="var(--art-dark)"/>
    </linearGradient>
  </defs>

  <rect class="label__background" width="1200" height="490" fill="var(--label-black)"/>

  <rect class="label__illustration" x="530" y="44" width="140" height="202" rx="4"
        fill="url(#art-tones)" role="img"
        aria-label="Engraved-style illustration of a Revolutionary War soldier and two modern soldiers advancing beneath a waving American flag"/>

  <text class="tagline" x="525" y="259" textLength="150" lengthAdjust="spacingAndGlyphs">ALL GAVE SOME, SOME GAVE ALL.</text>

  <text class="numeral" x="525" y="327" textLength="150" lengthAdjust="spacingAndGlyphs">250</text>

  <text class="headline headline--years" x="524" y="370" textLength="153" lengthAdjust="spacingAndGlyphs">YEARS OF</text>
  <text class="headline headline--unyielding" x="524" y="401" textLength="153" lengthAdjust="spacingAndGlyphs">UNYIELDING</text>
  <text class="headline headline--spirit" x="526" y="455" textLength="149" lengthAdjust="spacingAndGlyphs">SPIRIT</text>
</svg>
</body>
</html>
```